Jolly Paws Business Card Update

I have a business card which I love. I want to keep the same logo, colours, font and style. I want to upgrade the scripting and remove some elements and add others.
On the front side under Services - remove the existing wording and insert - Providing individual coaching strategies to create happy, healthy and social canine companions
Under Denise Carvell amend the current wording to read: Qualified in Dog Behavioural Training, Natural Animal Healthcare and Animal Health Science
On the reverse side to remove the web address.

```html
<!DOCTYPE html>
<html lang="en">
<head>
<meta charset="utf-8">
<title>Jolly Paws – Business Card</title>
<link href="https://fonts.googleapis.com/css2?family=Open+Sans:ital,wght@0,400;0,600;1,400&family=Arimo:wght@400;700&display=swap" rel="stylesheet">
<style>
  :root{
    --page:#e4e1dd;
    --card:#f2f3f5;
    --card-edge:#dfe2e7;
    --navy:#2b3585;
    --blue:#2f49a3;
    --teal:#1fa6cc;
    --red:#a8232d;
    --ink:#111111;
    --white:#ffffff;
    --label:#d4d6da;
    --ring-fill:#f6efd9;
  }
  html,body{margin:0;padding:0;}
  body{
    width:1200px;height:1054px;overflow:hidden;
    background:var(--page);
    position:relative;
  }
  .card{
    position:absolute;left:60px;top:202px;
    width:1080px;height:650px;
    border-radius:24px;overflow:hidden;
    background:linear-gradient(180deg,var(--card),#e9ebef);
    box-shadow:0 0 0 1px var(--card-edge);
  }
  .card__header{
    position:absolute;left:0;top:0;width:100%;height:190px;
    background:linear-gradient(90deg,var(--teal) 0%,#2a6fbf 40%,var(--blue) 100%);
  }
  .services{
    position:absolute;right:50px;top:30px;
    margin:0;text-align:right;
    font-family:"Arimo",Arial,sans-serif;
    font-size:27px;line-height:34px;color:var(--white);
  }
  .services__label{font-weight:700;color:var(--label);}
  .owner{position:absolute;left:55px;top:210px;}
  .owner__name{
    margin:0;font-family:"Open Sans",sans-serif;font-weight:600;
    font-size:42px;line-height:52px;color:var(--navy);
  }
  .owner__quals{
    margin:4px 0 0;font-family:"Open Sans",sans-serif;font-style:italic;
    font-size:25px;line-height:37px;color:var(--navy);
  }
  .contact{
    position:absolute;left:55px;top:420px;margin:0;padding:0;list-style:none;
    font-family:"Open Sans",sans-serif;font-size:26px;line-height:39px;color:var(--navy);
  }
  .contact__item{display:flex;align-items:center;gap:22px;}
  .contact__icon{width:26px;height:26px;flex:none;}
  .tagline{
    position:absolute;left:55px;top:582px;margin:0;
    font-family:"Arimo",Arial,sans-serif;font-size:26px;color:var(--ink);
  }
  .brand{
    position:absolute;left:708px;top:227px;width:316px;height:316px;
    display:flex;align-items:center;justify-content:center;
  }
  .brand__circle{
    position:absolute;inset:0;border-radius:50%;
    background:var(--ring-fill);
  }
  .brand__name{
    position:relative;font-family:"Open Sans",sans-serif;font-weight:600;
    font-size:40px;color:var(--navy);
  }
</style>
</head>
<body>
  <section class="card">
    <div class="card__header" role="img" aria-label="Decorative blue header band with red wave accents"></div>

    <p class="services"><span class="services__label">SERVICES:</span> Providing Individual<br>Coaching Strategies to Create<br>Happy, Healthy and Social<br>Canine Companions</p>

    <div class="owner">
      <h1 class="owner__name">Denise Carvell</h1>
      <p class="owner__quals">Qualified in Dog Behavioural Training,<br>Natural Animal Healthcare and<br>Animal Health Science</p>
    </div>

    <ul class="contact">
      <li class="contact__item">
        <svg class="contact__icon" viewBox="0 0 26 26"><rect x="7" y="2" width="12" height="22" rx="2" fill="#a8232d"/><rect x="9" y="5" width="8" height="7" fill="#f2f3f5"/></svg>
        0412 555 207
      </li>
      <li class="contact__item">
        <svg class="contact__icon" viewBox="0 0 26 26"><rect x="2" y="6" width="22" height="15" fill="#a8232d"/><path d="M2 6 L13 15 L24 6" fill="none" stroke="#f2f3f5" stroke-width="2"/></svg>
        jollypaws1@mailbox.net
      </li>
      <li class="contact__item">
        <svg class="contact__icon" viewBox="0 0 26 26"><circle cx="13" cy="13" r="10" fill="#a8232d"/><path d="M3 13 H23 M13 3 V23 M6 7 H20 M6 19 H20" stroke="#f2f3f5" stroke-width="1.5"/></svg>
        www.jollypaws1.net
      </li>
    </ul>

    <div class="brand">
      <span class="brand__circle"></span>
      <span class="brand__name">Jolly Paws</span>
    </div>

    <p class="tagline">Promoting communication and connection between dogs and their families</p>
  </section>
</body>
</html>
```